House-share and Room Rental Website (With Focus on the Bedroom Landing Page)

Looking for website design for our House-share (executive accommodation) and room rental business.

Our company name is: Lodgivo could also be written as LodGivo or lodgivo. Either is fine .. just looking for a nice clean catchy logo to go with the design.

EXAMPLES
These are examples of other websites in this field that are doing well. this is a kind of baseline.
https://nestpartners-example.com.au/
https://www.bunkora-example.com/
https://www.dwelzy-example.com/
https://www.habiquo-example.net/
https://www.cohabiscout-example.com.au/

Our business model is to rent rooms to people looking for high-quality accommodation. We fill the gap between those looking to rent rooms and those with rooms to rent. However, our model is slightly different from those already on the market as we looking to fill a massive gap in the market delivering upmarket rooms for rent.(Executive Accommodation) also in the back end will be coupled with a self management process in the back end.

We offer executive style accommodation that stands out above the rest. With special extras like fire safety.. and management processes that create happier homes. We are looking for a web design package that can help us grow and scale our business. We need a design that is captivating

Our MAIN focus is having a room landing page that stands out from the rest... The core of our business will rely on the promotion of the rooms in a share house... so the whole design relies on the BEDROOM landing page to drive results.

Target Market(s)

We have 2 markets we are aiming at ... the first market is people offering rooms to rent who want the highest rental return. The second market is people looking to rent safe, high-quality rooms, in houses that are well managed and looked after.

Industry/Entity Type

Share Economy

Logo Text

LodGivo

Number of Pages Required

5+ page

Font styles to use
Sans Serif

Colors
3276b5

Requirements
Must have
• A messaging system whereby we can create direct communication between those offering rooms and those looking for rooms.
• A call to action that says " Schedule an Inspection"
• Landing page for promoting rooms
• A home page for showing stock.
• Profile page for those selling rooms
• Profile page for those looking for rooms.
• A scheduling calendar for booking inspections
Nice to have
• Pages where new residents can lock in a room.. pay bond and rents.. and sign contracts
• Notifications
• SMS capabilities in the backend.
Should not have
• No script or handwriting fonts.

```html
<!DOCTYPE html>
<html lang="en">
<head>
<meta charset="utf-8">
<title>Lodgivo – Bedroom</title>
<link href="https://fonts.googleapis.com/css2?family=Barlow:wght@400;500&display=swap" rel="stylesheet">
<style>
:root{
  --brand:#3276b5;
  --ink:#2b2b2b;
  --muted:#555;
  --line:#dcdcdc;
  --band:#f0f0f0;
  --white:#fff;
  --icon:#4a7bb7;
}
*{box-sizing:border-box;margin:0;padding:0}
html,body{width:738px;height:1200px;overflow:hidden;background:var(--white)}
body{position:relative;font-family:'Barlow',sans-serif;color:var(--ink)}
h1,h2,h4{font-weight:400}
/* header */
.site-header{position:absolute;left:0;top:0;width:738px;height:51px;border-bottom:1px solid #cfcfcf;background:var(--white)}
.logo{position:absolute;font-size:15px;font-weight:400;color:var(--brand);letter-spacing:.2px}
.site-header .logo{left:106px;top:15px}
.nav{position:absolute;top:19px;left:309px;font-size:9px;color:#444}
.nav span{position:absolute;white-space:nowrap}
.cta{position:absolute;left:533px;top:14px;width:98px;height:22px;border:1px solid #333;border-radius:12px;font-size:7px;display:flex;align-items:center;justify-content:center;color:#222}
/* room band */
.room-band{position:absolute;left:0;top:51px;width:738px;height:445px;background:var(--band)}
.hero-photo{position:absolute;left:0;top:86px;width:455px;height:258px;
  background:
    radial-gradient(ellipse 38% 30% at 50% 8%,rgba(255,246,220,.75),rgba(255,246,220,0) 70%),
    radial-gradient(ellipse 22% 16% at 37% 40%,rgba(255,226,170,.55),rgba(255,226,170,0) 70%),
    radial-gradient(ellipse 22% 16% at 70% 40%,rgba(255,226,170,.5),rgba(255,226,170,0) 70%),
    linear-gradient(180deg,#cdc4b2 0%,#bdb19c 35%,#9fa0ad 55%,#8f8e96 72%,#b3aea8 88%,#9d9a97 100%)}
.thumb{position:absolute;width:61px;height:52px}
.room-title{position:absolute;left:475px;top:84px;font-size:17.5px;letter-spacing:.5px;color:#222}
.addr-label{position:absolute;left:475px;top:115px;font-size:12px;display:flex;align-items:center;gap:3px}
.addr{position:absolute;left:475px;top:135px;font-size:7.5px;line-height:13.5px;color:#333}
.price-label{position:absolute;left:476px;top:171px;font-size:12px;color:#333}
.price{position:absolute;left:558px;top:170px;font-size:12.5px;font-weight:500;color:var(--brand)}
.spec{position:absolute;left:475px;width:140px;height:24px;border-bottom:1px solid var(--line);font-size:8.6px;color:#222}
.spec b{font-weight:500}
.spec span{position:absolute;left:83px;top:0;width:120px;font-weight:400;color:var(--muted);white-space:nowrap}
/* amenities */
.sec-title{position:absolute;top:531px;font-size:11.5px;color:#222}
.amenity{position:absolute;display:flex;align-items:center;gap:9px;font-size:7.8px;color:#333;line-height:10px}
.amenity svg{width:18px;height:18px;flex:none}
.transport{position:absolute;left:350px;top:565px;display:flex;align-items:center;gap:8px;font-size:7.8px;color:#333}
.transport svg{width:19px;height:19px}
.distance{position:absolute;left:350px;top:602px;font-size:7.8px;color:#333}
/* map */
.map{position:absolute;left:0;top:744px;width:738px;height:224px;
  background:
    radial-gradient(ellipse 6% 22% at 85% 30%,#aacbe8,rgba(170,203,232,0) 80%),
    radial-gradient(ellipse 25% 40% at 10% 60%,#d3e2c2,rgba(211,226,194,0) 75%),
    radial-gradient(ellipse 20% 35% at 30% 35%,#dbe6cc,rgba(219,230,204,0) 75%),
    linear-gradient(90deg,#d9e6cc 0%,#e6e8d8 30%,#ecebe0 55%,#eae9dd 75%,#d6e2d6 90%,#bcd6ec 100%)}
/* footer */
.site-footer .logo{left:106px;top:988px;color:#222}
.social{position:absolute;top:990px;left:560px;display:flex;gap:4px}
.social i{display:block;width:15px;height:15px;border-radius:50%}
.rule{position:absolute;left:106px;width:526px;height:1px;background:#ddd}
.f-col{position:absolute;top:1038px}
.f-col h4{font-size:8.8px;color:#222;margin-bottom:9px}
.f-col li{list-style:none;font-size:6.6px;color:#444;line-height:11.5px}
.copyright{position:absolute;top:1178px;left:0;width:738px;text-align:center;font-size:7px;color:#333}
</style>
</head>
<body>

<header class="site-header">
  <div class="logo">Lodgivo</div>
  <nav class="nav">
    <span style="left:0">Home</span>
    <span style="left:43px">About</span>
    <span style="left:88px">Rooms</span>
    <span style="left:136px">News</span>
    <span style="left:178px">Contact</span>
  </nav>
  <div class="cta">Schedule an Inspection</div>
</header>

<section class="room-band"></section>

<div class="hero-photo" role="img" aria-label="Bright master bedroom with tufted bed, framed artwork and bedside lamps"></div>

<div class="thumb" style="left:0;top:349px;background:linear-gradient(180deg,#9aa1a8,#4d5257)" role="img" aria-label="Open living area"></div>
<div class="thumb" style="left:66px;top:349px;background:linear-gradient(160deg,#5a4634,#e7d8c6 55%,#d9c3a6)" role="img" aria-label="Folded towels with flower"></div>
<div class="thumb" style="left:132px;top:349px;background:linear-gradient(180deg,#c9c3bc,#7a6a62 60%,#5b4c48)" role="img" aria-label="Dining chairs"></div>
<div class="thumb" style="left:197px;top:349px;background:linear-gradient(160deg,#c7975f,#7d5e45 55%,#4c3a2d)" role="img" aria-label="Lamp-lit lounge"></div>
<div class="thumb" style="left:263px;top:349px;background:linear-gradient(90deg,#cfc6bc,#b09c8a 60%,#e5e2de)" role="img" aria-label="Wardrobe with clothes"></div>
<div class="thumb" style="left:329px;top:349px;background:linear-gradient(180deg,#f2f2f3,#cfd0d3)" role="img" aria-label="Kitchen tap"></div>
<div class="thumb" style="left:394px;top:349px;background:linear-gradient(180deg,#dcd7d0,#5a524c 55%,#2f2c2a)" role="img" aria-label="Modern kitchen"></div>

<div class="thumb" style="left:0;top:407px;background:linear-gradient(160deg,#e3d9c8,#b38c5e 55%,#6f8a4a)" role="img" aria-label="Dining room with plants"></div>
<div class="thumb" style="left:66px;top:407px;background:linear-gradient(180deg,#b8cde0,#6b8fae 60%,#3f6384)" role="img" aria-label="Rain shower head"></div>
<div class="thumb" style="left:132px;top:407px;background:linear-gradient(135deg,#a86a3f,#7b4a2c 55%,#4a2c1b)" role="img" aria-label="Timber staircase"></div>
<div class="thumb" style="left:197px;top:407px;background:linear-gradient(180deg,#e5e2dc,#3a3a3c 40%,#d8d3c9 70%)" role="img" aria-label="Television wall unit"></div>
<div class="thumb" style="left:263px;top:407px;background:linear-gradient(180deg,#2f3944,#4a5562 55%,#b7b9bb)" role="img" aria-label="Lounge with sofa"></div>
<div class="thumb" style="left:329px;top:407px;background:linear-gradient(90deg,#3d2615,#8a5c34 50%,#3d2615)" role="img" aria-label="Walk-in closet shelving"></div>
<div class="thumb" style="left:394px;top:407px;background:linear-gradient(160deg,#e8eaec,#9aa2a8 55%,#6a7278)" role="img" aria-label="Glass shower bathroom"></div>

<h1 class="room-title">BEDROOM NAME</h1>
<div class="addr-label">
  <svg width="8" height="10" viewBox="0 0 8 10"><path d="M4 0a3.6 3.6 0 0 0-3.6 3.6C.4 6.3 4 10 4 10s3.6-3.7 3.6-6.4A3.6 3.6 0 0 0 4 0zm0 5a1.4 1.4 0 1 1 0-2.8A1.4 1.4 0 0 1 4 5z" fill="#333"/></svg>
  Adress
</div>
<p class="addr">Lorem isom 48 Harbor Crest Lane<br>Maple, TX.70000 dummy</p>
<div class="price-label">Rental price</div>
<div class="price">: $250.00</div>

<div class="spec" style="top:210px"><b>Gender Preference</b><span>: Male</span></div>
<div class="spec" style="top:234px"><b>Size of room</b><span>: 1200Sqm</span></div>
<div class="spec" style="top:258px"><b>Bathroom</b><span>&nbsp;: Private</span></div>
<div class="spec" style="top:282px"><b>Parking</b><span>&nbsp;: Private</span></div>
<div class="spec" style="top:306px"><b>Smoking</b><span>&nbsp;: Male</span></div>
<div class="spec" style="top:330px"><b>Minimum contract</b><span>&nbsp;: Usually 3 months</span></div>
<div class="spec" style="top:354px"><b>Bed size</b><span>: 12X12</span></div>
<div class="spec" style="top:378px"><b>Type of housemates</b><span>: Professionals</span></div>
<div class="spec" style="top:402px"><b>Room type</b><span>: Private</span></div>
<div class="spec" style="top:426px"><b>Internet speed</b><span>: 180 kbps</span></div>
<div class="spec" style="top:448px;border:none"><b>Utilities</b><span>: Included</span></div>

<h2 class="sec-title" style="left:106px">ROOM Amenities</h2>
<h2 class="sec-title" style="left:350px">Public amenities..</h2>

<div class="amenity" style="left:109px;top:569px">
  <svg viewBox="0 0 18 18" fill="none" stroke="var(--icon)" stroke-width="1"><rect x="4" y="2" width="10" height="6" rx="1"/><path d="M3 9h12M5 9v4h8V9M9 13v3M6 16h6"/></svg>
  <span>Furnished/<br>unfurnished</span>
</div>
<div class="amenity" style="left:226px;top:570px">
  <svg viewBox="0 0 18 18" fill="none" stroke="var(--icon)" stroke-width="1"><rect x="2" y="4" width="14" height="9"/><path d="M7 16l2-3 2 3z"/></svg>
  <span>&nbsp;TV</span>
</div>
<div class="amenity" style="left:109px;top:606px">
  <svg viewBox="0 0 18 18" fill="none" stroke="var(--icon)" stroke-width="1"><path d="M2 10h14M3 10v6M15 10v6M9 10v4h6"/><rect x="5" y="4" width="6" height="4"/></svg>
  <span>Study Desk /<br>&nbsp;Workstation</span>
</div>
<div class="amenity" style="left:226px;top:607px">
  <svg viewBox="0 0 18 18" fill="none" stroke="var(--icon)" stroke-width="1"><rect x="2" y="2" width="14" height="14"/><path d="M9 2v14M2 6h14M7 10v2M11 10v2"/></svg>
  <span>&nbsp;Wardrobe</span>
</div>
<div class="amenity" style="left:109px;top:644px">
  <svg viewBox="0 0 18 18" fill="none" stroke="var(--icon)" stroke-width="1"><rect x="1" y="4" width="16" height="11"/><path d="M1 8h16M4 4v11M14 4v11"/></svg>
  <span>Storage space</span>
</div>
<div class="amenity" style="left:226px;top:644px">
  <svg viewBox="0 0 18 18" fill="none" stroke="var(--icon)" stroke-width="1"><path d="M3 10a5 5 0 0 1 10 0zM8 5V2h7M15 2v3M5 12v2M8 12v3M11 12v2"/></svg>
  <span>Ensuite shower</span>
</div>
<div class="amenity" style="left:109px;top:680px">
  <svg viewBox="0 0 18 18" fill="none" stroke="var(--icon)" stroke-width="1"><path d="M3 16L14 3M15 2l1 3-3 3M3 2l12 14M3 2l3 1-1 3"/></svg>
  <span>Kitchenette</span>
</div>

<div class="transport">
  <span>Transport Options</span>
  <svg viewBox="0 0 19 19" fill="none" stroke="#8a9bb0" stroke-width="1"><rect x="4" y="2" width="11" height="12" rx="2"/><path d="M4 8h11M6 17l2-3M13 17l-2-3"/><circle cx="7" cy="11" r=".8"/><circle cx="12" cy="11" r=".8"/></svg>
  <svg viewBox="0 0 19 19" fill="none" stroke="#8a9bb0" stroke-width="1"><rect x="3" y="2" width="13" height="13" rx="1.5"/><path d="M3 8h13M6 15v2M13 15v2"/><circle cx="6" cy="12" r=".8"/><circle cx="13" cy="12" r=".8"/></svg>
  <svg viewBox="0 0 19 19" fill="none" stroke="var(--icon)" stroke-width="1.2"><path d="M2 13V9l3-4h9l3 4v4z"/><path d="M2 9h15"/><circle cx="6" cy="14" r="1.5"/><circle cx="13" cy="14" r="1.5"/></svg>
</div>
<p class="distance">Location or distance to the city- 120 km</p>

<div class="map" role="img" aria-label="Road map showing the route and driving time to the property"></div>

<footer class="site-footer">
  <div class="logo">Lodgivo</div>
  <div class="social" aria-label="Social links">
    <i style="background:#2d4a8a"></i><i style="background:#2e9ad8"></i><i style="background:#1f6ea8"></i><i style="background:#e0443a"></i>
  </div>
  <div class="rule" style="top:1023px"></div>

  <div class="f-col" style="left:106px">
    <h4>Room amenities</h4>
    <ul><li>Furnished/unfurnished</li><li>TV</li><li>Storage space</li><li>Study Desk / Workstation</li><li>Wardrobe</li><li>Ensuite shower</li><li>Kitchenette</li></ul>
  </div>
  <div class="f-col" style="left:270px">
    <h4>Rooms</h4>
    <ul><li>Lorem ipsum dolo</li><li>Consectetur adipiscing elit.</li><li>Fusce eget leo tincid</li><li>Donec consequat</li><li>Praesent elementum</li><li>Jmauris posueret</li><li>Aenean a ex eu lectu</li></ul>
  </div>
  <div class="f-col" style="left:399px">
    <h4>&nbsp;</h4>
    <ul><li>Lorem ipsum dolo</li><li>Consectetur adipiscing elit.</li><li>Fusce eget leo tincid</li><li>Donec consequat</li><li>Praesent elementum</li><li>Jmauris posueret</li><li>Aenean a ex eu lectu</li></ul>
  </div>
  <div class="f-col" style="left:545px">
    <h4>Other Links</h4>
    <ul><li>Lorem ipsum dolo</li><li>Consectetur adipiscing elit.</li><li>Fusce eget leo tincid</li><li>Donec consequat</li><li>Praesent elementum</li><li>Jmauris posueret</li><li>Aenean a ex eu lectu</li></ul>
  </div>

  <div class="rule" style="top:1162px"></div>
  <p class="copyright">Copyright 2019 Lodgivo. All Rights Reserved</p>
</footer>

</body>
</html>
```